BRAMBLEFORD CONSTRUCTIONS B-Card

I currently have a b-card design but will be removing the image (tree) from the logo and have text only.
I want the card to be classy and strong within the building and construction industry.
I will be using Spot UV on the cards as per the attached examples. I will also send through some sketched ideas that I have in mind.
The color blue is similar to the image (No. 6) attached images

Target Market(s)

middle to maturre aged.
Home Owners / Renovators and Builders

Industry/Entity Type

Construction

Contact Information for Business Card

BRAMBLEFORD CONSTRUCTIONS
Name: Gareth Pennick
Title: Project Manager
Mobile: 0427 351 804
Office: (08) 9316 5172
Address: 47C Corvell Street, Malaga WA 6090
Email: info@bramblefordhomes.com.au
PO Box: 3817 Malaga WA 6944

Colors
0592cd
33a6d7
85cae6
1b1b1b

Requirements
Must have
• 1. It must have spot UV on the front of card, maybe back of card too
• 2. I really like the blue on image 6. (or at least a really cool electric blue against the charcoal grey background)
• 3. The font must be slimline and modern. Easy to read
• 4. There must be no black used on the card... Only greys and dark charcoal greys
• 5. Use only the text from the logo "Brambleford Constructions" Not the image of the tree. I am wanting the b-cards to be more masculine.
Nice to have
• 1. I like the design concept on image 6. but happy to see what else you can do with the Spot UV
• 2. Unless you have a really cool idea of the image of the tree (from previous logo) Spot UV somewhere in the design concept thats original and different then I am keen to see what you come up with
• 3. Try changing the color of the logo eg. full white or Blue and white
• 4. Another option is to have the Brambleford Logo on the front of card with the spot UV in the background of text which we specialise in eg, Roofing, Ceiling, Insulation, Gutter Guards, Electrical, Insurance etc and we can add or reduce items as required. Similar to image 12.
Should not have
• Do not include the image of the tree from previous logo. unless you have a really cool idea of Spot UV somewhere in the design concept thats original and different.

```html
<!DOCTYPE html>
<html lang="en">
<head>
<meta charset="utf-8">
<title>Brambleford Constructions Business Card</title>
<link rel="stylesheet" href="https://fonts.googleapis.com/css2?family=Questrial&display=swap">
<style>
  :root {
    --stage: #e9e7e3;
    --brand-blue: #2062b4;
    --brand-blue-deep: #1c57a2;
    --pattern-blue: #2a6cbd;
    --paper: #ffffff;
    --ink: #4a4a4a;
    --frame-white: #ffffff;
  }
  * { margin: 0; padding: 0; box-sizing: border-box; }
  html, body {
    width: 1200px; height: 843px; overflow: hidden;
    background: var(--stage);
    font-family: "Questrial", "Century Gothic", sans-serif;
  }
  .stage { position: relative; width: 1200px; height: 843px; }

  .card { position: absolute; box-shadow: 0 6px 18px rgba(40,40,40,.18); }

  /* Back of card */
  .card-back {
    left: 90px; top: 250px; width: 600px; height: 343px;
    background: var(--brand-blue);
    overflow: hidden;
  }
  .card-back .spot-uv-field {
    position: absolute; inset: 0;
    background: linear-gradient(135deg, var(--pattern-blue), var(--brand-blue-deep));
  }
  .card-back .frame {
    position: absolute; inset: 10px;
    border: 1.5px solid var(--frame-white);
  }
  .services {
    position: absolute; inset: 0;
    display: flex; flex-direction: column; align-items: center; justify-content: center;
    color: var(--frame-white); font-size: 19px; line-height: 1.45; letter-spacing: .3px;
  }

  /* Front of card */
  .card-front {
    left: 790px; top: 121px; width: 343px; height: 600px;
    background: var(--paper);
  }
  .card-front .frame {
    position: absolute; inset: 10px;
    border: 2px solid var(--brand-blue);
  }
  .front-content {
    position: absolute; inset: 0;
    display: flex; flex-direction: column; align-items: center;
    padding-top: 62px; text-align: center; color: var(--ink);
  }
  .wordmark { color: var(--brand-blue); line-height: 1; }
  .wordmark-name { display: block; font-size: 40px; letter-spacing: .5px; }
  .wordmark-sub { display: block; font-size: 14.5px; letter-spacing: 7px; margin-top: 6px; margin-right: -7px; }

  .icon { display: block; width: 18px; height: 18px; fill: var(--brand-blue); margin: 0 auto 6px; }

  .person { margin-top: 44px; }
  .person-name { color: var(--brand-blue); font-size: 24px; }
  .person-title { font-size: 16px; margin-top: 3px; color: var(--ink); }

  .address { margin-top: 34px; font-size: 15.5px; line-height: 1.35; }
  .phones { margin-top: 30px; font-size: 16px; line-height: 1.3; }
  .phones .line + .line { margin-top: 12px; }
  .email { margin-top: 24px; font-size: 14px; }
</style>
</head>
<body>
<main class="stage">

  <section class="card card-back" aria-label="Back of business card">
    <div class="spot-uv-field" role="img" aria-label="Spot UV pattern of repeated company name on blue"></div>
    <div class="frame"></div>
    <div class="services">
      <p>Roofing | Ceiling | Insulation</p>
      <p>Gutter Guards | Electrical | Insurance etc</p>
    </div>
  </section>

  <section class="card card-front" aria-label="Front of business card">
    <div class="frame"></div>
    <div class="front-content">
      <h1 class="wordmark">
        <span class="wordmark-name">BRAMBLEFORD</span>
        <span class="wordmark-sub">CONSTRUCTIONS</span>
      </h1>

      <div class="person">
        <svg class="icon" viewBox="0 0 20 20" aria-hidden="true"><circle cx="10" cy="6" r="4.2"/><path d="M2 19c0-5 3.6-7.5 8-7.5s8 2.5 8 7.5z"/></svg>
        <p class="person-name">Gareth Pennick</p>
        <p class="person-title">Project Manager</p>
      </div>

      <div class="address">
        <svg class="icon" viewBox="0 0 20 20" aria-hidden="true"><path d="M10 1a6.5 6.5 0 0 0-6.5 6.5C3.5 12.5 10 19 10 19s6.5-6.5 6.5-11.5A6.5 6.5 0 0 0 10 1zm0 9a2.5 2.5 0 1 1 0-5 2.5 2.5 0 0 1 0 5z"/></svg>
        <p>47C Corvell Street</p>
        <p>Malaga WA 6090</p>
        <p>PO Box: 3817 Malaga</p>
        <p>WA 6944</p>
      </div>

      <div class="phones">
        <div class="line">
          <svg class="icon" viewBox="0 0 20 20" aria-hidden="true"><path d="M5.2 2.5l2.6 3.2-1.6 2a10 10 0 0 0 6.1 6.1l2-1.6 3.2 2.6-1.8 2.7C9.5 17.4 2.6 10.5 2.5 4.3z"/></svg>
          <p>(08) 9316 5172</p>
        </div>
        <div class="line">
          <svg class="icon" viewBox="0 0 20 20" aria-hidden="true"><path d="M6 1h8a1.5 1.5 0 0 1 1.5 1.5v15A1.5 1.5 0 0 1 14 19H6a1.5 1.5 0 0 1-1.5-1.5v-15A1.5 1.5 0 0 1 6 1zm0.5 2.5v11h7v-11z"/></svg>
          <p>0427 351 804</p>
        </div>
      </div>

      <div class="email">
        <svg class="icon" viewBox="0 0 20 20" aria-hidden="true"><path d="M2 4h16v12H2z M3.5 5.5l6.5 5 6.5-5" fill="none" stroke="#2062b4" stroke-width="2"/></svg>
        <p>info@bramblefordhomes.com.au</p>
      </div>
    </div>
  </section>

</main>
</body>
</html>
```